Redo a PPT pres. - Real Estate in Brazil - Socially equitable investments in Social Housing

We need to redo the presentation attached. It is an institutional presentation to attract local and foreign investors to invest in Brazilian Social Housing Projects structured by our company "TLR".
A middle class of 100 million, a housing deficit of 9M, a strong political will & positive income generation trends constitute grounds for a significant demand in social housing.
This make a perfect scheme for investors to invest in Brazilian Social Housing.
"TLR", is a consulting "boutique" focused in Brazilian real estate, specialized in structuring, analyzing and originating Brazilian social housing projects.
TLR is part of the group TLB. TLB is structured to create value through each step of the residential real estate business - structuring, financing, sales, marketing and technology.
We would like to see designs that use mainly the color blue. The final design should communicate financial safety and professionalism. In order to reach our needs, the designer will need to have basic understanding of finance and investment in order to highlight the most important information.
The idea is to receive back the PPT with each page redesigned and an homogeneous identity.
To all designers,
Target Market(s)
Institutional Investors and wealthy individuals
Industry/Entity Type
Residential
Look and feel

```html
<!DOCTYPE html>
<html lang="en">
<head>
<meta charset="utf-8">
<title>TLR – Social Housing in Brazil</title>
<link href="https://fonts.googleapis.com/css2?family=Arimo:wght@400;700&display=swap" rel="stylesheet">
<style>
  :root{
    --backdrop:#0c0d10;
    --sky-top:#5c7aa6;
    --sky-mid:#2f4f7f;
    --city-deep:#1b2c4c;
    --banner:rgba(24,32,52,0.78);
    --banner-solid:#1c2335;
    --white:#ffffff;
    --lime:#8cc63f;
    --green-1:#a6d16a;
    --green-2:#8cc63f;
    --green-3:#6aa534;
    --green-4:#c3e09a;
    --ink:#3b3f45;
    --muted:#8a9099;
  }
  *{box-sizing:border-box;margin:0;padding:0}
  html,body{width:1200px;height:520px;overflow:hidden;background:var(--backdrop)}
  body{position:relative;font-family:"Arimo",Arial,sans-serif}

  .slide{position:absolute;top:60px;width:531px;height:398px;overflow:hidden}
  .slide--cover{left:46px}
  .slide--method{left:623px;background:var(--white)}

  .city-photo{position:absolute;inset:0;
    background:linear-gradient(180deg,var(--sky-top) 0%,var(--sky-mid) 38%,var(--city-deep) 70%,#2b4469 100%)}

  /* cover */
  .cover-banner{position:absolute;left:68px;top:0;width:390px;height:392px}
  .cover-title{position:absolute;left:68px;top:78px;width:390px;text-align:center;color:var(--white);
    font-weight:700;font-size:26px;line-height:34px;letter-spacing:1px}
  .cover-subtitle{position:absolute;left:68px;top:158px;width:390px;text-align:center;color:var(--lime);
    font-size:13px;line-height:17px;letter-spacing:.5px}
  .brand-box{position:absolute;left:225px;top:230px;width:76px;height:32px;background:var(--white);
    display:flex;align-items:center;justify-content:center;gap:5px}
  .brand-box .mark{width:7px;height:7px;background:#2b4a8c}
  .brand-box .name{color:#2b4a8c;font-weight:700;font-size:15px;letter-spacing:.5px}
  .cover-note{position:absolute;right:10px;bottom:6px;color:var(--lime);font-size:5px;letter-spacing:.3px}

  /* method slide */
  .side-panel{position:absolute;left:0;top:0;width:193px;height:398px}
  .logo-tab{position:absolute;left:52px;top:0;width:68px;height:74px}
  .logo-tab-name{position:absolute;left:52px;top:30px;width:68px;text-align:center;color:var(--white);
    font-size:15px;letter-spacing:.5px}
  .method-heading{position:absolute;left:18px;top:198px;width:170px;color:var(--white);
    font-weight:700;font-size:16px;line-height:19px}
  .tagline-ribbon{position:absolute;left:0;top:352px;width:210px;height:24px}
  .tagline{position:absolute;left:18px;top:358px;color:var(--lime);font-size:8.5px}

  .step-ring{position:absolute;left:193px;top:0;width:338px;height:398px}
  .step{position:absolute;width:88px;height:88px;display:flex;align-items:center;justify-content:center;
    text-align:center;color:var(--ink);font-size:7.5px;line-height:9.5px;padding:0 12px}

  .pager{position:absolute;right:22px;bottom:14px;display:flex;align-items:center;gap:4px;color:#5a6fa8;font-size:9px;font-weight:700}
</style>
</head>
<body>

<section class="slide slide--cover">
  <div class="city-photo" role="img" aria-label="Aerial photograph of a dense high-rise city skyline beside a harbour, in blue tones"></div>
  <svg class="cover-banner" viewBox="0 0 390 392" aria-hidden="true">
    <polygon points="0,0 390,0 390,392 195,262 0,392" fill="var(--banner)"/>
  </svg>
  <h1 class="cover-title">SOCIAL HOUSING<br>IN BRAZIL</h1>
  <p class="cover-subtitle">HIGH YIELD RETURN FOR<br>A QUASI SOVEREIGN RISK</p>
  <div class="brand-box"><span class="mark"></span><span class="name">TLR</span></div>
  <p class="cover-note">CONFIDENTIAL DRAFT</p>
</section>

<section class="slide slide--method">
  <div class="side-panel city-photo" role="img" aria-label="Photograph of a high-rise city skyline at dusk, in deep blue tones"></div>
  <svg class="logo-tab" viewBox="0 0 68 74" aria-hidden="true">
    <polygon points="0,0 68,0 68,74 34,56 0,74" fill="var(--banner-solid)"/>
  </svg>
  <div class="logo-tab-name">TLR</div>
  <h2 class="method-heading">HOW TO INVEST<br>IN SOCIAL HOUSING<br>IN BRAZIL?</h2>
  <svg class="tagline-ribbon" viewBox="0 0 210 24" aria-hidden="true">
    <polygon points="0,0 200,0 210,12 200,24 0,24" fill="var(--banner-solid)"/>
    <rect x="0" y="0" width="4" height="24" fill="var(--lime)"/>
  </svg>
  <p class="tagline">A socially conscious &amp; lucrative investment</p>

  <div class="step-ring">
    <svg width="338" height="398" viewBox="0 0 338 398" aria-hidden="true" style="position:absolute;inset:0">
      <g fill="none" stroke-width="3">
        <circle cx="175" cy="105" r="42" stroke="var(--green-2)"/>
        <circle cx="242" cy="133" r="42" stroke="var(--green-4)"/>
        <circle cx="270" cy="200" r="42" stroke="var(--green-2)"/>
        <circle cx="242" cy="267" r="42" stroke="var(--green-3)"/>
        <circle cx="175" cy="295" r="42" stroke="var(--green-1)"/>
        <circle cx="108" cy="267" r="42" stroke="var(--green-2)"/>
        <circle cx="80" cy="200" r="42" stroke="var(--green-3)"/>
        <circle cx="108" cy="133" r="42" stroke="var(--green-4)"/>
      </g>
    </svg>
    <div class="step" style="left:131px;top:61px">Building housing units for low to middle-class buyers</div>
    <div class="step" style="left:198px;top:89px">Investing in individual projects Management</div>
    <div class="step" style="left:226px;top:156px">Specialised International and local team</div>
    <div class="step" style="left:198px;top:223px">Co-investing with local / mid-size developers</div>
    <div class="step" style="left:131px;top:251px">Co-financed by government</div>
    <div class="step" style="left:64px;top:223px">Equity participation of R$2-10 millions</div>
    <div class="step" style="left:36px;top:156px">Time Horizon 3-4 years</div>
    <div class="step" style="left:64px;top:89px">Target IRR 25-50%</div>
  </div>

  <div class="pager">
    <svg width="6" height="9" viewBox="0 0 6 9" aria-hidden="true"><polyline points="5,1 1,4.5 5,8" fill="none" stroke="var(--muted)" stroke-width="1.5"/></svg>
    <span>01</span>
    <svg width="6" height="9" viewBox="0 0 6 9" aria-hidden="true"><polyline points="1,1 5,4.5 1,8" fill="none" stroke="var(--muted)" stroke-width="1.5"/></svg>
  </div>
</section>

</body>
</html>
```